Wordpress 6 pages GLAM design for hair salon

Hi guys.
I need a glam & easy to navigate web design for my (women only) new hair salon.
I have a logo. You can see in attached files.
I like 3d backgrounds.
My favourite colours choice: any variety of pink(hot & very soft), white, black, grey.
I would like to see website very feminine, glamorous & kind of old Hollywood and Dorinda Calloway inspired.
Of course it should have plug ins, like social media, map, security etc.
My website now: http://velmoracoiffure.example

Designs what I like:
http://torvinellastudio.example
http://pelurabeautyloft.example
http://www.quillfernvisualworks.example/boutique-graphic-web-folio.html
Updates

Target Market(s)

WOMEN

Industry/Entity Type

Boutique

Requirements
Should not have
• any cartoon or other characters!

```html
<!DOCTYPE html>
<html lang="en">
<head>
<meta charset="utf-8">
<title>Velmora Coiffure</title>
<link rel="stylesheet" href="https://fonts.googleapis.com/css2?family=Oswald:wght@300;400&family=Open+Sans:ital,wght@0,400;1,400&family=Bilbo+Swash+Caps&display=swap">
<style>
:root{
  --pink:#e34d8c;
  --pink-deep:#c0366f;
  --pink-panel:#c64878;
  --pink-frame:#e77aa6;
  --ink:#232323;
  --grey:#555;
  --white:#fff;
}
*{box-sizing:border-box;margin:0;padding:0}
html,body{width:1029px;height:1200px;overflow:hidden}
body{
  position:relative;
  background:radial-gradient(ellipse at 50% 30%,#fafafa 0%,#ececec 70%,#e2e2e2 100%);
  font-family:"Open Sans",sans-serif;color:var(--grey);
}
.page{position:absolute;left:103px;top:0;width:823px;height:1080px;background:var(--white);box-shadow:0 0 4px rgba(0,0,0,.25)}
.masthead{position:absolute;left:0;top:0;width:823px;height:163px;
  background:linear-gradient(180deg,#d23a78 0%,#e56a9c 55%,#fbe5ee 100%)}
.brand{position:absolute;left:50%;top:12px;transform:translateX(-50%);width:216px;height:144px;border-radius:50%;
  background:var(--white);display:flex;align-items:center;justify-content:center;text-align:center}
.brand span{font-family:"Oswald",sans-serif;font-weight:400;color:var(--pink-deep);font-size:22px;line-height:1}
.nav{position:absolute;left:8px;top:171px;width:806px;height:42px;background:var(--ink);outline:2px solid var(--ink);border:2px solid var(--white)}
.nav ul{list-style:none;display:flex;justify-content:space-around;height:100%;align-items:center;padding:0 40px}
.nav a{font-family:"Oswald",sans-serif;color:var(--white);text-decoration:none;font-size:15px;text-transform:uppercase}
.flourish{position:absolute;background:linear-gradient(90deg,rgba(214,61,124,.15),rgba(214,61,124,.75),rgba(214,61,124,.15));border-radius:10px}
.hero{position:absolute;left:8px;top:247px;width:806px;height:320px;border:4px solid var(--pink-frame)}
.hero-photo{position:absolute;inset:0;background:linear-gradient(90deg,#8e4434 0%,#a3553f 45%,#c9a17a 68%,#b28d72 85%,#9a7b6b 100%)}
.hero h1{position:absolute;left:27px;top:53px;width:400px;font-family:"Oswald",sans-serif;font-weight:400;color:var(--white);font-size:36px;line-height:40px;text-shadow:1px 1px 3px rgba(0,0,0,.55)}
.btn{position:absolute;left:27px;top:193px;height:42px;padding:0 18px;background:var(--pink);color:var(--white);font-family:"Oswald",sans-serif;font-size:20px;line-height:42px;text-decoration:none}
.dots{position:absolute;left:27px;top:272px;display:flex;gap:5px}
.dots i{width:17px;height:17px;border-radius:50%;background:rgba(255,255,255,.55)}
.dots i:first-child{background:var(--white)}
.script{font-family:"Bilbo Swash Caps",cursive;color:var(--ink);font-weight:400}
.welcome-title{position:absolute;left:0;top:610px;width:823px;text-align:center;font-size:30px}
.rule{position:absolute;top:658px;height:1px;background:var(--pink-deep)}
.welcome-text{position:absolute;left:68px;top:693px;width:687px;text-align:center;font-size:11.3px;line-height:22px;color:var(--grey)}
.col{position:absolute;top:800px;width:257px}
.col h2{text-align:center;font-size:23px;height:26px;line-height:26px}
.col .flourish{height:12px;width:50px;top:8px}
.panel{position:absolute;top:26px;left:0;width:257px;height:214px;background:var(--pink-panel);border:4px solid var(--pink-frame)}
.col .flourish.bottom{top:244px}
.shot{position:absolute;border:4px solid var(--pink-frame)}
.post{padding:14px 18px 0;color:var(--white)}
.post h3{font-family:"Oswald",sans-serif;font-weight:400;font-size:18px;margin-bottom:4px}
.post p{font-size:11.3px;line-height:17px;margin-bottom:22px}
.cal{position:absolute;left:10px;top:14px;width:229px;background:#2a2a2a;color:var(--white);font-size:11px}
.cal caption{background:linear-gradient(#fff,#e6e6e6);color:var(--pink-deep);height:27px;line-height:27px;font-size:11px}
.cal table{width:100%;border-collapse:collapse;text-align:center}
.cal th{font-weight:400;height:22px}
.cal td{height:22px}
.cal tr:nth-child(even) td{background:#3e3e3e}
.cal tr.last td{height:12px;background:#2a2a2a}
.footer{position:absolute;left:103px;top:1100px;width:823px;height:70px}
.legal{position:absolute;left:9px;top:24px;font-family:"Oswald",sans-serif;font-size:13px;line-height:22px;color:var(--pink-deep);font-weight:300}
.legal b{font-weight:300;color:var(--ink)}
.sub-title{position:absolute;left:392px;top:0;font-size:23px}
.sub-form{position:absolute;left:392px;top:36px;width:217px;height:31px;border:1px solid #ccc;display:flex;background:var(--white)}
.sub-form span{flex:1;font-style:italic;font-size:11px;color:#888;line-height:29px;padding-left:8px}
.sub-form i{width:28px;background:var(--pink-panel);display:flex;align-items:center;justify-content:center}
.connect-title{position:absolute;left:700px;top:0;font-size:23px}
.socials{position:absolute;left:700px;top:36px;display:flex;gap:6px}
.socials span{width:31px;height:31px;background:#2b2b2b;color:var(--white);font-family:"Open Sans",sans-serif;font-size:7px;display:flex;align-items:center;justify-content:center}
</style>
</head>
<body>
<div class="page">
  <header class="masthead" role="img" aria-label="Pink swirling floral ornament band">
    <div class="brand"><span>Velmora Coiffure</span></div>
  </header>
  <nav class="nav"><ul>
    <li><a href="#">Home</a></li><li><a href="#">About Us</a></li><li><a href="#">Services</a></li>
    <li><a href="#">Gallery</a></li><li><a href="#">Blog</a></li><li><a href="#">Contact</a></li>
  </ul></nav>
  <div class="flourish" style="left:235px;top:222px;width:355px;height:24px" role="img" aria-label="Pink floral ornament"></div>
  <section class="hero">
    <div class="hero-photo" role="img" aria-label="Woman with long blonde curls before a red brick wall"></div>
    <h1>Certified Hair Stylist with European and Canadian experience</h1>
    <a class="btn" href="#">Book Your Appointment</a>
    <div class="dots"><i></i><i></i><i></i><i></i></div>
  </section>
  <div class="flourish" style="left:12px;top:566px;width:180px;height:26px" role="img" aria-label="Pink floral corner ornament"></div>
  <div class="flourish" style="left:632px;top:566px;width:180px;height:26px" role="img" aria-label="Pink floral corner ornament"></div>

  <h2 class="welcome-title script">Welcome to Our Website</h2>
  <div class="rule" style="left:8px;width:318px"></div>
  <div class="flourish" style="left:332px;top:650px;width:160px;height:18px" role="img" aria-label="Pink floral divider ornament"></div>
  <div class="rule" style="left:497px;width:318px"></div>
  <p class="welcome-text">Our salon is based on the belief that our customers' needs are of the utmost importance. Our team is committed to meeting those needs. As a result, a high percentage of our business is from repeat customers and referrals.<br>We would welcome the opportunity to earn your trust and deliver you the best service in the industry!</p>

  <section class="col" style="left:8px">
    <div class="flourish" style="left:0" role="img" aria-label="Pink floral ornament"></div>
    <div class="flourish" style="right:0" role="img" aria-label="Pink floral ornament"></div>
    <h2 class="script">Our Gallery</h2>
    <div class="panel">
      <div class="shot" style="left:7px;top:19px;width:140px;height:166px;background:linear-gradient(135deg,#d9c9a8,#b7a07c 60%,#8f8274)" role="img" aria-label="Model with long crimped blonde hair"></div>
      <div class="shot" style="left:157px;top:19px;width:83px;height:78px;background:linear-gradient(135deg,#3a2a26,#6e4a3e)" role="img" aria-label="Model with glossy dark waves"></div>
      <div class="shot" style="left:157px;top:106px;width:83px;height:79px;background:linear-gradient(135deg,#d2a36a,#b96f4a)" role="img" aria-label="Model with vintage pinned curls"></div>
    </div>
    <div class="flourish bottom" style="left:0" role="img" aria-label="Pink floral ornament"></div>
    <div class="flourish bottom" style="right:0" role="img" aria-label="Pink floral ornament"></div>
  </section>

  <section class="col" style="left:284px">
    <div class="flourish" style="left:0" role="img" aria-label="Pink floral ornament"></div>
    <div class="flourish" style="right:0" role="img" aria-label="Pink floral ornament"></div>
    <h2 class="script">Recent Posts</h2>
    <div class="panel">
      <article class="post"><h3>December 14, 2013</h3><p>“The Polished Everyday” by Celia Marchetti. A stylist`s notes on effortless shine..</p></article>
      <article class="post" style="padding-top:0"><h3>December 14, 2013</h3><p>Hair that makes you look like YOU DON`T HAVE A DIME: - Unruly frizz (where...</p></article>
    </div>
    <div class="flourish bottom" style="left:0" role="img" aria-label="Pink floral ornament"></div>
    <div class="flourish bottom" style="right:0" role="img" aria-label="Pink floral ornament"></div>
  </section>

  <section class="col" style="left:558px">
    <div class="flourish" style="left:0" role="img" aria-label="Pink floral ornament"></div>
    <div class="flourish" style="right:0" role="img" aria-label="Pink floral ornament"></div>
    <h2 class="script">Calender</h2>
    <div class="panel">
      <div class="cal"><table>
        <caption>JANUARY 2014</caption>
        <tr><th>M</th><th>T</th><th>W</th><th>T</th><th>F</th><th>S</th><th>S</th></tr>
        <tr><td></td><td></td><td>1</td><td>2</td><td>3</td><td>4</td><td>5</td></tr>
        <tr><td>6</td><td>7</td><td>8</td><td>9</td><td>10</td><td>11</td><td>12</td></tr>
        <tr><td>13</td><td>14</td><td>15</td><td>16</td><td>17</td><td>18</td><td>19</td></tr>
        <tr><td>20</td><td>21</td><td>22</td><td>23</td><td>24</td><td>25</td><td>26</td></tr>
        <tr><td>27</td><td>28</td><td>29</td><td>30</td><td>31</td><td></td><td></td></tr>
        <tr class="last"><td colspan="7"></td></tr>
      </table></div>
    </div>
    <div class="flourish bottom" style="left:0" role="img" aria-label="Pink floral ornament"></div>
    <div class="flourish bottom" style="right:0" role="img" aria-label="Pink floral ornament"></div>
  </section>
</div>

<footer class="footer">
  <p class="legal">Copyright © 2014 <b>Velmora Coiffure</b> | All Right Reserved<br>Privacy Policy</p>
  <h2 class="sub-title script">Email Subscribe</h2>
  <div class="sub-form"><span>Enter Email</span><i><svg width="10" height="12" viewBox="0 0 10 12"><path d="M2 1l6 5-6 5" fill="none" stroke="#fff" stroke-width="2.5"/></svg></i></div>
  <h2 class="connect-title script">Connect Us</h2>
  <div class="socials"><span style="background:#1e4f7a">Parlour</span><span style="background:#2a9fd6">Gossip</span><span>Glimmer</span></div>
</footer>
</body>
</html>
```